Event Center Website

We need a new website design for an upscale event center in Reno, Nevada. The building hosts everything from weddings to corporate events to funerals and it competitively more expensive. The overall look and feel is consistent with a Lake Tahoe aesthetic. The current site can be viewed at www.themaplehallevents.com. They are looking for a major upgrade. A sample site they like is www.cliffsidelodgestay.com. We have new photography available (some attached). The site should be very visual. A site map is attached as well for direction on what elements the site should include as well as labels for navigation. I am looking for a home page and sample interior page. Any questions, let me know. Thanks.
Updates

I have added some photography of the center itself for use rather than stock photography. Thanks!

Target Market(s)

Brides, professionals, high-income

Industry/Entity Type

Building

Requirements
Must have
• See site map

```html
<!DOCTYPE html>
<html lang="en">
<head>
<meta charset="utf-8">
<title>Maple Hall at Willow Bend</title>
<link href="https://fonts.googleapis.com/css2?family=Fondamento&family=Roboto+Condensed:wght@400;700&family=Open+Sans:wght@400&family=Acme&display=swap" rel="stylesheet">
<style>
:root{
  --orange:#d2771f;
  --orange-band:rgba(210,119,31,.82);
  --brown:#4b2a12;
  --brown-dark:#42240f;
  --menu:rgba(96,60,28,.86);
  --ink:#3a2410;
  --white:#ffffff;
}
*{margin:0;padding:0;box-sizing:border-box}
html,body{width:1200px;height:807px;overflow:hidden;background:var(--white)}
.page{position:relative;width:1200px;height:807px;overflow:hidden}
.hero-photo{position:absolute;left:0;top:0;width:1200px;height:632px;
  background:
   radial-gradient(ellipse at 50% 30%,rgba(150,170,90,.55),transparent 60%),
   linear-gradient(180deg,#6f7a3c 0%,#8a6a3e 30%,#b79a80 55%,#a98070 75%,#5d5555 100%);}
.header-band{position:absolute;left:0;top:37px;width:1200px;height:66px;background:var(--orange-band)}
.brand{position:absolute;left:124px;top:20px;width:193px;height:61px;background:var(--brown);
  display:flex;align-items:center;gap:10px;padding-left:10px}
.brand-mark{width:14px;height:14px;background:var(--white)}
.brand-name{font-family:"Fondamento",serif;font-size:24px;color:var(--white);line-height:1}
.nav{position:absolute;top:37px;left:0;height:66px;font-family:"Roboto Condensed",sans-serif;font-size:15px;color:var(--brown);text-transform:uppercase}
.nav-item{position:absolute;top:29px;white-space:nowrap}
.nav-item.active{top:0;height:66px;width:105px;background:var(--menu);color:var(--white);padding-top:29px;text-align:center}
.dropdown{position:absolute;left:465px;top:103px;width:105px;background:var(--menu);font-family:"Open Sans",sans-serif;font-size:13px;color:var(--white)}
.dropdown li{list-style:none;height:36px;line-height:36px;padding-left:20px;border-bottom:1px solid rgba(255,255,255,.08)}
.headline{position:absolute;left:124px;top:348px;height:51px;padding:0 12px 0 6px;background:rgba(60,45,40,.72);
  font-family:"Fondamento",serif;font-size:41px;color:var(--white);line-height:51px;white-space:nowrap}
.headline-name{position:absolute;left:124px;top:413px;height:51px;padding:0 16px 0 6px;background:rgba(60,45,40,.72);
  font-family:"Roboto Condensed",sans-serif;font-weight:700;font-size:38px;color:var(--white);line-height:51px}
.cta{position:absolute;left:125px;top:474px;width:209px;height:38px;background:var(--orange);
  font-family:"Roboto Condensed",sans-serif;font-size:14px;color:var(--white);text-align:center;line-height:38px;text-transform:uppercase}
.rule{position:absolute;top:617px;height:14px;background:var(--orange)}
.badge{position:absolute;top:572px;width:106px;height:106px;border-radius:50%;background:var(--white);
  display:flex;justify-content:center;padding-top:38px}
.footer{position:absolute;top:632px;left:0;width:1200px;height:138px;background:var(--white);font-family:"Acme",sans-serif;color:var(--ink)}
.footer-col{position:absolute;top:43px;font-size:17px;line-height:23px}
.links li{list-style:none;font-family:"Roboto Condensed",sans-serif;font-size:15px;line-height:21px;color:var(--brown);padding-left:26px;position:relative}
.links li::before{content:"»";position:absolute;left:0;color:var(--orange);font-size:16px}
.contact-row{display:flex;align-items:center;gap:10px;margin-bottom:8px}
.tour{text-align:center;color:var(--brown)}
.bottom-bar{position:absolute;left:0;top:770px;width:1200px;height:37px;background:var(--brown-dark);
  font-family:"Acme",sans-serif;font-size:14px;color:var(--white);text-align:center;line-height:37px}
</style>
</head>
<body>
<div class="page">
  <div class="hero-photo" role="img" aria-label="Photo of a sweetheart table with rosette linens, pink sashed chairs and flowers before tall windows"></div>
  <div class="header-band"></div>
  <div class="brand"><span class="brand-mark"></span><span class="brand-name">Maple Hall</span></div>
  <nav class="nav">
    <span class="nav-item" style="left:414px">Home</span>
    <span class="nav-item active" style="left:465px">About Us</span>
    <span class="nav-item" style="left:585px">Gallery</span>
    <span class="nav-item" style="left:676px">Weddings</span>
    <span class="nav-item" style="left:778px">Meetings</span>
    <span class="nav-item" style="left:877px">Other Events</span>
    <span class="nav-item" style="left:1005px">Caterings</span>
  </nav>
  <ul class="dropdown">
    <li>Lena Bio</li><li>Mara Bio</li><li>Tessa Bio</li><li>Owen Bio</li>
  </ul>
  <div class="headline">Thank you for your interest in</div>
  <div class="headline-name">MAPLE HALL</div>
  <div class="cta">Schedual an appointment</div>

  <div class="rule" style="left:124px;width:217px"></div>
  <div class="rule" style="left:370px;width:217px"></div>
  <div class="rule" style="left:614px;width:217px"></div>
  <div class="rule" style="left:858px;width:217px"></div>

  <div class="badge" style="left:177px">
    <svg width="28" height="24" viewBox="0 0 28 24"><path d="M14 2 2 12h4v10h6v-6h4v6h6V12h4z" fill="#4b2a12"/></svg>
  </div>
  <div class="badge" style="left:423px">
    <svg width="30" height="30" viewBox="0 0 30 30" fill="none" stroke="#4b2a12" stroke-width="4"><rect x="3" y="5" width="12" height="9" rx="4.5" transform="rotate(45 9 9.5)"/><rect x="15" y="16" width="12" height="9" rx="4.5" transform="rotate(45 21 20.5)"/><line x1="12" y1="12" x2="18" y2="18"/></svg>
  </div>
  <div class="badge" style="left:667px">
    <svg width="32" height="24" viewBox="0 0 32 24" fill="none" stroke="#4b2a12" stroke-width="2.5"><rect x="2" y="2" width="28" height="20" rx="2"/><path d="M2 4l14 11L30 4"/></svg>
  </div>
  <div class="badge" style="left:911px">
    <svg width="28" height="28" viewBox="0 0 28 28" stroke="#4b2a12" stroke-width="5" stroke-linecap="round"><line x1="14" y1="3" x2="14" y2="25"/><line x1="4.5" y1="8.5" x2="23.5" y2="19.5"/><line x1="4.5" y1="19.5" x2="23.5" y2="8.5"/></svg>
  </div>

  <footer class="footer">
    <div class="footer-col" style="left:145px">Maple Hall | Willow Bend<br>&nbsp;2210 Ridge Road, Suite C<br>Carson, Nevada 89701</div>
    <ul class="footer-col links" style="left:425px;top:45px">
      <li>FAQ</li><li>TESTIMONIAL</li><li>CONTACT US</li>
    </ul>
    <div class="footer-col" style="left:630px;top:42px">
      <div class="contact-row"><svg width="17" height="13" viewBox="0 0 17 13"><rect width="17" height="13" rx="2" fill="#d2771f"/><path d="M1 2l7.5 6L16 2" fill="none" stroke="#fff" stroke-width="1.5"/></svg>info@maplehall.com</div>
      <div class="contact-row"><svg width="17" height="17" viewBox="0 0 17 17"><rect width="17" height="17" rx="3" fill="#d2771f"/><path d="M5 4c-1 1 0 4 2.5 6.5S12 14 13 13l-2-2-1.5 1C8 11 6 9 5 7.5L6 6z" fill="#fff"/></svg>+1.775.555.0142</div>
    </div>
    <div class="footer-col tour" style="left:870px;top:41px;width:182px">Click here to See Our<br>Virtual Tour<br>
      <svg width="32" height="24" viewBox="0 0 32 24" style="margin-top:4px"><path d="M8 22a7 7 0 0 1-1-13.9A9 9 0 0 1 24 7a7.5 7.5 0 0 1 0 15z" fill="#d2771f"/><path d="M16 9v8m-4-4 4 4 4-4" stroke="#fff" stroke-width="2.5" fill="none"/></svg>
    </div>
  </footer>
  <div class="bottom-bar">All Rights reserved 2014-2015</div>
</div>
</body>
</html>
```